BRTL web site redesign

Coastal Linkage Engineering service (BRTL) is a diverse technology company specialising in design and installation of fibre optics, network convergence and building services, for commercial clients in Australia, we required a new design of our website to attract new clients, generate sales leads, and provide information about our services to the market. The site and should have a new technology look and feel and be designed in word press. our branding colour is blue.

Target Market(s)

New developments, Construction organisations, Commercial end users, IT managers, Consultants.

Industry/Entity Type

It Company

Number of Pages Required

5+ page

Font styles to use
Sans Serif

Colors
0292cd
3176b5

Requirements
Must have
• key pages.
• Home page with some sizzle, automated pictures running through, I like the look of this competitor website http://www.gleamwirex.com.au/ good clean menus and easy to navigate.
• Services page our key services are Fibre optics, Security, Building services,Electrical. I would like the same page layout (Design) for all our services, with a find out more link on each page, manly picture driven with text around our key messaging.
• About us page with space for company profile and directors pictures, bio and contact information.
• Certifications / Accreditations page with have over 20 certifications on different products from suppliers, and a number of licences from governing bodies.
• Current and past projects page with case studies and customer outcomes
• Contact us page with options around what services they require more information on, please keep in mind the site is around generating sales Leeds and being seen as an industry expert.
Nice to have
• RSS feeds, Linked in link, to be placed within the design, Consistent BRTL branding,Same colour blue as our logo Document library for education information, white papers, presentations etc,
• a new technology look and feel, mobile friendly.
Should not have
• boring layout, move away from our cuurent website http://www.brtlgroup.com.au/
• no e eCommerce store required.

```html
<!DOCTYPE html>
<html lang="en">
<head>
<meta charset="utf-8">
<title>BRTL – Communications Integration</title>
<link href="https://fonts.googleapis.com/css2?family=Open+Sans:wght@400;600;700&display=swap" rel="stylesheet">
<style>
:root{
  --brand:#0292cd;
  --brand-deep:#3176b5;
  --band:#3a80c4;
  --title:#1a8fc9;
  --ink:#333;
  --muted:#8a8a8a;
  --footer:#2b2b2b;
  --footer-text:#9a9a9a;
}
*{margin:0;padding:0;box-sizing:border-box}
html,body{width:796px;height:1200px;overflow:hidden;background:#fff}
body{position:relative;font-family:"Open Sans",sans-serif;color:var(--ink)}
.abs{position:absolute}

.topbar{left:0;top:0;width:796px;height:23px;background:var(--brand);color:#fff;font-size:8px}
.topbar .call{left:40px;top:7px}
.topbar .login{left:712px;top:7px;display:flex;align-items:center;gap:4px}

.header{left:0;top:23px;width:796px;height:57px;background:#fff}
.logo{position:absolute;left:40px;top:6px;display:flex;align-items:center;gap:5px;color:var(--brand-deep)}
.logo .mark{width:16px;height:16px;background:var(--brand-deep)}
.logo .name{font-size:30px;font-weight:700;line-height:1;letter-spacing:1px}
.logo-tag{position:absolute;left:40px;top:45px;font-size:4.2px;line-height:5px;color:var(--brand-deep);white-space:nowrap}
.nav{left:0;top:17px;width:796px;height:22px;font-size:9.6px;color:#333}
.nav a{position:absolute;top:0;height:22px;display:flex;align-items:center;white-space:nowrap;text-decoration:none;color:inherit}
.nav .home{left:279px;width:53px;border:1px solid #9cc9e6;border-radius:3px;color:var(--brand-deep);justify-content:center}
.caret{display:inline-block;margin-left:5px;margin-top:3px;border:3px solid transparent;border-top-color:#333}

.hero{left:0;top:80px;width:796px;height:356px;background:linear-gradient(90deg,#8c8a6c 0%,#5f6468 30%,#6f7478 55%,#9a9da0 80%,#b4b6b8 100%)}
.hero h1{left:0;width:796px;top:113px;text-align:center;color:#fff;font-size:22.5px;font-weight:600}
.hero p{left:0;width:796px;top:150px;text-align:center;color:#fff;font-size:12.8px;line-height:18.5px;font-weight:600}
.hero .cta{left:308px;top:207px;width:180px;height:31px;background:#0e8fd6;color:#fff;font-size:12.8px;display:flex;align-items:center;justify-content:center;border-radius:2px}
.hero .arrow{top:163px;color:#fff;font-size:22px;font-weight:700}

.welcome{left:0;width:796px;top:456px;text-align:center;font-size:22px;color:#333;font-weight:400}
.intro{left:72px;width:652px;top:490px;text-align:center;font-size:8.5px;line-height:14.6px;color:var(--muted)}
.whatwedo{left:0;width:796px;top:547px;text-align:center;font-size:22px;color:#333;font-weight:400}

.card{width:350px;height:140px;background:#fff;box-shadow:0 0 3px rgba(0,0,0,.18)}
.card .pic{position:absolute;left:0;top:0;width:150px;height:140px}
.card h3{position:absolute;left:170px;top:12px;font-size:11.6px;font-weight:400;color:var(--title);letter-spacing:.2px}
.card p{position:absolute;left:170px;top:34px;width:160px;font-size:7.4px;line-height:14.6px;color:var(--muted);text-align:justify}
.card .more{position:absolute;left:272px;top:104px;width:58px;height:19px;background:var(--brand-deep);color:#fff;font-size:8.8px;display:flex;align-items:center;justify-content:center;border-radius:2px}

.updates{left:0;top:917px;width:796px;height:68px;background:var(--band);color:#fff}
.updates .label{left:40px;top:25px;font-size:14px;font-weight:600}
.updates .email{left:158px;top:22px;width:163px;height:24px;background:#4a8fd0;border:1px solid #5b9ad6;font-size:6.5px;color:#d7e6f5;padding:7px 10px}
.updates .sub{left:351px;top:22px;width:104px;height:24px;background:#fff;color:var(--brand-deep);font-size:14px;font-weight:600;display:flex;align-items:center;justify-content:center}
.updates .connect{left:528px;top:25px;font-size:14px;font-weight:600}
.social{top:22px;width:28px;height:24px;background:#1e90e0}

.footer{left:0;top:985px;width:796px;height:182px;background:var(--footer);color:var(--footer-text)}
.footer h4{position:absolute;top:24px;font-size:14px;font-weight:400;color:#fff}
.footer .txt{position:absolute;font-size:8px;line-height:13.6px}
.news{position:absolute;left:264px;font-size:9px;color:#fff;line-height:13.6px}
.news .date{color:#1a8fd0;font-size:8px}
.news .b{position:absolute;left:0;top:0}
.news .t{padding-left:14px}
.contact b{color:#fff;font-weight:600}
.footer .c13{left:773px;top:8px;font-size:6.5px;color:#fff}
.footer .sitemap{left:712px;top:164px;font-size:7.5px;color:#ccc}

.bottom{left:0;top:1167px;width:796px;height:33px;background:var(--footer);border-top:1px solid #3a3a3a;color:#aaa;font-size:7.5px}
.bottom .copy{left:40px;top:12px}
.bottom .links{right:40px;top:12px;color:#ccc}
</style>
</head>
<body>

<div class="abs topbar">
  <span class="abs call">Call Us! &nbsp;1300 426 915</span>
  <span class="abs login"><svg width="6" height="7" viewBox="0 0 6 7"><rect x="0" y="3" width="6" height="4" fill="#fff"/><path d="M1.3 3V2a1.7 1.7 0 0 1 3.4 0v1" stroke="#fff" fill="none"/></svg>Login</span>
</div>

<header class="abs header">
  <div class="logo"><span class="mark"></span><span class="name">BRTL</span></div>
  <div class="logo-tag">COASTAL LINKAGE ENGINEERING SERVICE</div>
  <nav class="abs nav">
    <a class="home">Home</a>
    <a style="left:345px">About us</a>
    <a style="left:408px">Services<span class="caret"></span></a>
    <a style="left:477px">Certifications<span class="caret"></span></a>
    <a style="left:567px">Current &amp; Past Projects<span class="caret"></span></a>
    <a style="left:700px">Contact us</a>
  </nav>
</header>

<section class="abs hero" role="img" aria-label="Engineer holding a laptop beside a server rack with fibre cables">
  <h1 class="abs">BRTL is a Communications Integration Company</h1>
  <p class="abs">Incorporating the expertise of Data and Fibre Optic Communications, ICT and low voltage systems,<br>Security and Application Services.</p>
  <div class="abs cta">More Deatils About BRTL</div>
  <span class="abs arrow" style="left:40px">&#10094;</span>
  <span class="abs arrow" style="left:743px">&#10095;</span>
</section>

<h2 class="abs welcome">Welcome To BRTL</h2>
<p class="abs intro">BRTL is diversified technology company 100% Australian owned and operated, we provide Communication, Electrical, Security &amp; ICT services for residential and commercial customers. With over 100 years of combined industry knowledge we pride ourselves on innovated solutions that utilises technology advancements which delivers on our customer's expectations.</p>
<h2 class="abs whatwedo">What We Do</h2>

<article class="abs card" style="left:40px;top:589px">
  <div class="pic" role="img" aria-label="Glowing fibre optic strands" style="background:linear-gradient(135deg,#0a3f5c,#1a9cc4 55%,#07283a)"></div>
  <h3>FIBRE OPTICS</h3>
  <p>Temporibus autem quibusdam et aut officiis debitis aut rerum necessitatibus saepe eveniet ut et voluptates repudiandae sint et molestiae non recusandae..</p>
  <div class="more">Read More</div>
</article>
<article class="abs card" style="left:406px;top:589px">
  <div class="pic" role="img" aria-label="Digital padlock with light rays" style="background:radial-gradient(circle at 50% 50%,#bfe3ff,#3a7fd8 40%,#1a2f6a 85%)"></div>
  <h3>SECURITY</h3>
  <p>Temporibus autem quibusdam et aut officiis debitis aut rerum necessitatibus saepe eveniet ut et voluptates repudiandae sint et molestiae non recusandae..</p>
  <div class="more">Read More</div>
</article>
<article class="abs card" style="left:40px;top:748px">
  <div class="pic" role="img" aria-label="Glass facade of a commercial building" style="background:linear-gradient(135deg,#2f6d6a,#6aa3a0 50%,#c8d6d8)"></div>
  <h3>BUILDING SERVICES</h3>
  <p>Temporibus autem quibusdam et aut officiis debitis aut rerum necessitatibus saepe eveniet ut et voluptates repudiandae sint et molestiae non recusandae..</p>
  <div class="more">Read More</div>
</article>
<article class="abs card" style="left:406px;top:748px">
  <div class="pic" role="img" aria-label="Technician splicing coloured cables" style="background:linear-gradient(135deg,#5a5f63,#8a6a4a 45%,#2d3236)"></div>
  <h3>ELECTRICAL</h3>
  <p>Temporibus autem quibusdam et aut officiis debitis aut rerum necessitatibus saepe eveniet ut et voluptates repudiandae sint et molestiae non recusandae..</p>
  <div class="more">Read More</div>
</article>

<section class="abs updates">
  <span class="abs label">GET UPDATES</span>
  <div class="abs email">Enter Email Address.....</div>
  <div class="abs sub">Subscribe</div>
  <svg class="abs" style="left:460px;top:0" width="72" height="68"><line x1="70" y1="0" x2="2" y2="68" stroke="#fff" stroke-width="1" opacity=".7"/></svg>
  <span class="abs connect">CONNECT VIA:</span>
  <span class="abs social" style="left:630px" aria-label="Social link"></span>
  <span class="abs social" style="left:663px" aria-label="Social link"></span>
  <span class="abs social" style="left:695px" aria-label="Social link"></span>
  <span class="abs social" style="left:729px" aria-label="Social link"></span>
</section>

<footer class="abs footer">
  <span class="abs c13">C13</span>
  <h4 style="left:40px">About Us</h4>
  <p class="txt" style="left:40px;top:46px;width:171px;text-align:justify">Lorem ipsum dolor sit amet, consectetur adipiscing elit. Integer lorem quam, adipiscing condimentum tristique vel, eleifend sed turpis. Pellentesque cursus arcu id magna euismod in elementum purus molestie.</p>

  <h4 style="left:264px">Latest News</h4>
  <div class="news" style="top:48px"><span class="b">&raquo;</span><div class="t">Adipiscing condimentum tristique eleifend.<br><span class="date">December 17, 2014.</span></div></div>
  <div class="news" style="top:88px"><span class="b">&raquo;</span><div class="t">Adipiscing condimentum tristique eleifend.<br>Ab expedita sintpara<br><span class="date">December 26, 2014.</span></div></div>
  <div class="news" style="top:142px"><span class="b">&raquo;</span><div class="t">Adipiscing condimentum tristique eleifend.<br><span class="date">December 17, 2014.</span></div></div>

  <h4 style="left:503px">Services</h4>
  <p class="txt" style="left:503px;top:46px">Fibre optics<br>Security<br>Building services<br>Electrical</p>

  <h4 style="left:627px">Contact Info</h4>
  <p class="txt contact" style="left:627px;top:46px">Suite 4B. 12-14 Harbour Crescent<br>Ridgeview NSW 2160<br>PO Box 2284 NSW 1801<br><b>Telephone:</b> 1300 426 915<br><b>Email:</b> info@brtlmail.com</p>

  <span class="abs sitemap">&#10230;&nbsp; Site Map</span>
</footer>

<div class="abs bottom">
  <span class="abs copy">Copyright 2015 BRTL Group. All Rights Reserved.</span>
  <span class="abs links">Home &nbsp;/&nbsp; About us &nbsp;/&nbsp; Services &nbsp;/&nbsp; Certifications &nbsp;/&nbsp; Current &amp; Past Projects &nbsp;/&nbsp; Contact us</span>
</div>

</body>
</html>
```